creation of a business card design for a company specializing in the creation...

I would like to create a design for a professional business card on a black background and with the company's colors (I am attaching some files: including the logo in horizontal and centered format, I am also attaching a recent project design a T-shirt, this is the one I chose to give you an idea of my preferences.

we are in the process of developing a new website design, it is still in the development phase but it can be viewed at the following address: www.vantrelmo.be to give you other ideas about the company
you will see for yourself the subject of my main activity: company specializing in the construction of stairs

I would like a business card that stands out from the rest with a unique design

here is the informations
Name: Lucien Barthel
Function: Manager
Address: Rue Moulinet du Parc 42
7180 La Louvière
telephone: +32 468 219 804
email: info@rx7p.be
website: rx7p. be
social networks: Facebook, YouTube, TikTok, Instagram

Target Market(s)

customer who wants to have a beautiful staircase built

Industry/Entity Type

contruction d'escalier

Contact Information for Business Card

Adresse. Numero de telephone, site web, le texte : "Createur d'escalier", logo recto-verso, icone des reseaux sociaux

Requirements
Must have
• the mention: Stair creator
Nice to have
• an illustration of a designer staircase
Should not have
• do not distort the logo

```html
<!DOCTYPE html>
<html lang="fr">
<head>
<meta charset="utf-8">
<title>RX7P – cartes de visite</title>
<link rel="stylesheet" href="https://fonts.googleapis.com/css2?family=Montserrat:wght@400;500;700&family=Oswald:wght@600&display=swap">
<style>
  :root {
    --backdrop: #3b3b3b;
    --card: #131314;
    --edge: #5b8fb8;
    --accent: #5e98c6;
    --accent-deep: #24506e;
    --accent-soft: #8fb9d8;
    --ink: #f2f2f2;
    --muted: #9aa3ab;
  }
  * { box-sizing: border-box; margin: 0; padding: 0; }
  html, body { width: 1200px; height: 801px; overflow: hidden; }
  body {
    background: var(--backdrop);
    font-family: "Montserrat", sans-serif;
    color: var(--ink);
    display: flex;
    align-items: center;
    justify-content: center;
    gap: 40px;
  }
  .card {
    width: 540px;
    height: 327px;
    background: var(--card);
    border: 2px solid var(--edge);
    border-radius: 4px;
    position: relative;
    overflow: hidden;
  }

  /* Front: identity + contact */
  .card--front { display: flex; }
  .identity {
    width: 52%;
    display: flex;
    flex-direction: column;
    align-items: center;
    justify-content: center;
    gap: 12px;
  }
  .brand { display: flex; align-items: center; gap: 14px; }
  .brand__mark { width: 34px; height: 34px; background: var(--accent); }
  .brand__name {
    font-weight: 500;
    font-size: 54px;
    letter-spacing: 4px;
    color: var(--ink);
    line-height: 1;
  }
  .tagline {
    font-size: 12px;
    letter-spacing: 6px;
    color: var(--accent);
    text-transform: uppercase;
  }
  .divider {
    width: 1px;
    background: var(--edge);
    margin: 0;
    height: 100%;
    opacity: .8;
  }
  .contact {
    flex: 1;
    padding: 46px 26px 0 28px;
    font-size: 13px;
    line-height: 1.5;
  }
  .contact__name {
    font-weight: 700;
    font-size: 17px;
    text-transform: uppercase;
    color: var(--accent);
    letter-spacing: .5px;
  }
  .contact__role { margin-bottom: 14px; }
  .contact__address { margin-bottom: 14px; }
  .contact__line { display: flex; align-items: center; gap: 8px; }
  .contact__line svg { width: 12px; height: 12px; fill: var(--accent); flex: none; }

  /* Back: emblem */
  .card--back {
    display: flex;
    flex-direction: column;
    align-items: center;
    justify-content: center;
  }
  .slogan {
    font-family: "Oswald", sans-serif;
    font-weight: 600;
    font-size: 17px;
    letter-spacing: 1px;
    text-transform: uppercase;
    color: var(--ink);
    margin-bottom: 4px;
  }
  .emblem-art {
    width: 150px;
    height: 118px;
    border-radius: 75px 75px 8px 8px;
    background: radial-gradient(circle at 50% 45%, #8d9599 0%, #3d6b88 45%, var(--accent-deep) 80%);
  }
  .card--back .brand__name { font-size: 46px; margin-top: 6px; }
  .card--back .tagline { font-size: 11px; margin-top: 4px; }
  .reach {
    display: flex;
    align-items: center;
    gap: 10px;
    margin-top: 8px;
    font-size: 10.5px;
    color: var(--ink);
  }
  .reach__item { display: flex; align-items: center; gap: 4px; }
  .reach svg { width: 11px; height: 11px; fill: var(--accent); }
  .socials { display: flex; gap: 7px; margin-top: 7px; }
  .socials span {
    width: 12px; height: 12px; border-radius: 50%;
    background: var(--accent);
  }
</style>
</head>
<body>

  <section class="card card--front" aria-label="Carte de visite, recto">
    <div class="identity">
      <div class="brand">
        <span class="brand__mark"></span>
        <span class="brand__name">RX7P</span>
      </div>
      <p class="tagline">Original Staircases</p>
    </div>
    <div class="divider"></div>
    <div class="contact">
      <p class="contact__name">Lucien Barthel</p>
      <p class="contact__role">Manager</p>
      <p class="contact__address">Rue Moulinet du Parc 42<br>7180 La Louvière</p>
      <p class="contact__line">
        <svg viewBox="0 0 24 24" aria-hidden="true"><path d="M6.6 10.8a15 15 0 0 0 6.6 6.6l2.2-2.2c.3-.3.7-.4 1-.2 1.1.4 2.3.6 3.6.6.6 0 1 .4 1 1V20c0 .6-.4 1-1 1A17 17 0 0 1 3 4c0-.6.4-1 1-1h3.5c.6 0 1 .4 1 1 0 1.3.2 2.5.6 3.6.1.3 0 .7-.2 1z"/></svg>
        +32 468 219 804
      </p>
      <p class="contact__line">
        <svg viewBox="0 0 24 24" aria-hidden="true"><path d="M2 5h20v14H2zm2 2v.5l8 5 8-5V7z"/></svg>
        info@rx7p.be
      </p>
      <p class="contact__line">
        <svg viewBox="0 0 24 24" aria-hidden="true"><circle cx="12" cy="12" r="10"/></svg>
        rx7p.be
      </p>
    </div>
  </section>

  <section class="card card--back" aria-label="Carte de visite, verso">
    <p class="slogan">Créateur d'escalier</p>
    <div class="emblem-art" role="img" aria-label="Illustration d'un escalier suspendu aux marches grises dans un médaillon bleu"></div>
    <p class="brand__name">RX7P</p>
    <p class="tagline">Original Staircases</p>
    <div class="reach">
      <span class="reach__item">
        <svg viewBox="0 0 24 24" aria-hidden="true"><path d="M6.6 10.8a15 15 0 0 0 6.6 6.6l2.2-2.2c.3-.3.7-.4 1-.2 1.1.4 2.3.6 3.6.6.6 0 1 .4 1 1V20c0 .6-.4 1-1 1A17 17 0 0 1 3 4c0-.6.4-1 1-1h3.5c.6 0 1 .4 1 1 0 1.3.2 2.5.6 3.6.1.3 0 .7-.2 1z"/></svg>
        0468 219 804
      </span>
      <span class="reach__item">
        <svg viewBox="0 0 24 24" aria-hidden="true"><circle cx="12" cy="12" r="10"/></svg>
        RX7P.BE
      </span>
    </div>
    <div class="socials" aria-label="Réseaux sociaux">
      <span></span><span></span><span></span><span></span>
    </div>
  </section>

</body>
</html>
```